Re-Design an adult education portal

I need support to re-design an adult education portal. Currently the customer has an incomplete website which should be prepared in a new format.
I have the idea how to realize, but I have no clue how to design it. The hard thing is to have a "beautiful" website with available logo and main color. I hope you can support me.

Name of Website: moluvo (moluvo.ch)
Content: adult eduction for adult in safety at work, mountain climbing, dog school. various courses in different areas. But on old webpage is hard to find the different possibilities.
main color: Ral 6011 (green) -> #6C7C59
logo: you see on top of website the logo (2 dogs and a mountain with a colour gradient).

new website: for new webpage I decided to have a navigation for each section of education. In the main area I would like to have some pictures to give an idea what content is behind. At the moment it looks terrible, so I decided to use you as support for me to make the webpage prettier :). And maybe you have an better idea how to make it great. -> current state of new web page: https://moluvo.perch-net.ch/

Target Market(s)

adult eduction for adult in safety at work, mountain climbing, dog school

Number of Pages Required

1 page

Font styles to use
Serif
Sans Serif

Requirements
Must have
• As main color is set "Ral 6011" (green) -> #6C7C59

```html
<!DOCTYPE html>
<html lang="de">
<head>
<meta charset="utf-8">
<title>moluvo – Ausbildungs- und Kurspartner</title>
<link href="https://fonts.googleapis.com/css2?family=Fjalla+One&family=Josefin+Sans:wght@400;600&family=Playfair+Display:wght@400;700&display=swap" rel="stylesheet">
<style>
:root{
  --green:#6C7C59;
  --brown:#8B5E34;
  --dark:#30363c;
  --ink:#2b2b2b;
  --muted:#5a5a5a;
  --paper:#ffffff;
  --soft:#f3f3f1;
}
*{box-sizing:border-box;margin:0;padding:0}
html,body{width:1200px;height:3552px;overflow:hidden}
body{position:relative;background:var(--paper);font-family:'Josefin Sans',sans-serif;color:var(--ink)}
.abs{position:absolute}

/* hero */
.hero{left:0;top:0;width:1200px;height:730px;clip-path:polygon(0 0,100% 0,100% 640px,0 730px);
  background:linear-gradient(180deg,#4f5a4a 0%,#6f7466 35%,#8b8676 60%,#5b5a50 100%)}
.hero-shade{left:0;top:0;width:1200px;height:730px;clip-path:polygon(0 0,100% 0,100% 640px,0 730px);
  background:linear-gradient(180deg,rgba(0,0,0,.25),rgba(0,0,0,0) 30%,rgba(0,0,0,.2))}
.brand{left:112px;top:0;width:230px;height:132px;background:#fff;display:flex;align-items:center;justify-content:center;gap:10px}
.brand-dot{width:14px;height:14px;border-radius:50%;background:var(--green)}
.brand-name{font-family:'Playfair Display',serif;font-weight:700;font-size:40px;color:var(--green)}
.nav{right:60px;top:20px;display:flex;gap:26px;font-size:15px;color:#fff;letter-spacing:.3px}
.hero-title{left:0;width:1200px;top:388px;text-align:center;font-family:'Fjalla One',sans-serif;font-size:46px;color:#fff}
.hero-sub{left:0;width:1200px;top:450px;text-align:center;font-size:23px;line-height:30px;color:#fff}
.btn{display:inline-block;border:2px solid #fff;border-radius:20px;font-size:13px;letter-spacing:1.5px;padding:9px 20px 6px;color:#fff}
.hero-btn{left:523px;top:562px;background:rgba(108,124,89,.85)}
.dots{left:574px;top:620px;display:flex;gap:10px}
.dots span{width:11px;height:11px;border-radius:50%;background:rgba(255,255,255,.5)}
.dots span:first-child{background:#fff}

/* services */
.deco{font-family:'Playfair Display',serif;color:#ececec;font-size:190px;line-height:1}
.section-title{font-family:'Playfair Display',serif;font-size:50px;color:var(--ink);text-align:center;width:1200px;left:0}
.tab{width:258px;height:260px}
.tab.green{background:var(--green)}
.tab.brown{background:var(--brown)}
.tab-label{position:absolute;right:6px;top:14px;writing-mode:vertical-rl;font-size:13px;letter-spacing:1.5px;color:#fff;font-weight:600}
.card-img{width:258px;height:230px}
.card-name{font-size:17px;font-weight:600;color:var(--ink);line-height:22px}
.card-text{font-size:14px;color:var(--muted);line-height:19px}

/* about */
.about-frame{left:140px;top:2210px;width:440px;height:400px;border:14px solid var(--green)}
.about-img{left:112px;top:2236px;width:440px;height:400px;background:linear-gradient(160deg,#5d6a72,#8a7a62 55%,#4d4a3e)}
.about-title{left:688px;top:2240px;font-family:'Playfair Display',serif;font-size:56px}
.about-text{left:688px;top:2338px;width:420px;font-size:15px;line-height:22px;color:var(--muted);text-align:justify}

/* goal band */
.goal{left:0;top:2700px;width:1200px;height:480px;background:var(--brown);clip-path:polygon(0 50px,100% 0,100% 430px,0 480px)}
.goal-text{left:0;width:1200px;top:2890px;text-align:center;font-family:'Playfair Display',serif;font-size:38px;line-height:46px;color:#fff}
.goal-btn{left:527px;top:3004px;background:var(--green)}

/* footer */
.footer{left:0;top:3150px;width:1200px;height:402px;background:var(--dark);clip-path:polygon(0 30px,100% 0,100% 100%,0 100%)}
.foot-brand{left:455px;top:3196px;width:290px;height:152px;background:#fff;display:flex;align-items:center;justify-content:center;gap:12px}
.foot-brand .brand-name{font-size:46px}
.contact{left:0;width:1200px;top:3438px;display:flex;justify-content:center;gap:48px;font-size:16px;color:#fff}
.contact span{display:flex;align-items:center;gap:8px}
.copy{left:0;width:1200px;top:3504px;text-align:center;font-size:15px;color:#e8e8e8}
</style>
</head>
<body>

<!-- hero -->
<div class="abs hero" role="img" aria-label="Foto: zwei Kursleiter mit Hunden im Freien vor Felsen und Bäumen"></div>
<div class="abs hero-shade"></div>
<div class="abs brand"><span class="brand-dot"></span><span class="brand-name">moluvo.ch</span></div>
<nav class="abs nav"><span>Arbeitssicherheit</span><span>Erste Hilfe</span><span>Hundeschule</span><span>CZV</span><span>Bergausbildung</span><span>Kontakt</span></nav>
<h1 class="abs hero-title">Ihr Ausbildungs- und Kurspartner</h1>
<p class="abs hero-sub">Wir bieten Ihnen Wünschen entsprechende<br>Ausbildungen, zielorientiert und Ihrem Können<br>und Wissen angepasst.</p>
<span class="abs btn hero-btn">LEARN MORE</span>
<div class="abs dots"><span></span><span></span><span></span></div>

<!-- services -->
<div class="abs deco" style="left:540px;top:770px">W</div>
<h2 class="abs section-title" style="top:846px">WE SERVE</h2>

<!-- row 1 -->
<div class="abs tab green" style="left:162px;top:968px"><span class="tab-label">STAPLERKURSE</span></div>
<div class="abs card-img" style="left:112px;top:996px;background:linear-gradient(150deg,#d9d4cc,#b88a6a 60%,#7c6a5a)" role="img" aria-label="Foto: Kursteilnehmerin am Laptop"></div>
<div class="abs" style="left:112px;top:1240px"><div class="card-name">STAPLERKURSE</div><div class="card-text">Grundausbildung</div></div>

<div class="abs tab brown" style="left:486px;top:968px"><span class="tab-label">PSAgA</span></div>
<div class="abs card-img" style="left:436px;top:996px;background:linear-gradient(150deg,#cfd6dc,#e9e9e9 50%,#a87c52)" role="img" aria-label="Foto: Person in Schutzausrüstung"></div>
<div class="abs" style="left:436px;top:1240px"><div class="card-name">PSAgA</div><div class="card-text">Persönliche Schutzausrüstung<br>gegen Abstürze (PSAgA)</div></div>

<div class="abs tab green" style="left:810px;top:968px"><span class="tab-label">HUBARBEITSBÜHNE</span></div>
<div class="abs card-img" style="left:760px;top:996px;background:linear-gradient(160deg,#6b9bc8,#9fc0de 50%,#c9a24a)" role="img" aria-label="Foto: Hubarbeitsbühne vor blauem Himmel"></div>
<div class="abs" style="left:760px;top:1240px"><div class="card-name">HUBARBEITSBÜHNEN</div><div class="card-text">Bedienerschulung<br>Bedienerschulung / CZV</div></div>

<!-- row 2 -->
<div class="abs tab brown" style="left:162px;top:1310px"><span class="tab-label">HUNDESCHULE</span></div>
<div class="abs card-img" style="left:112px;top:1338px;background:linear-gradient(150deg,#7c8a5e,#b7ae96 55%,#8a7358)" role="img" aria-label="Foto: Hund beim Agility-Training"></div>
<div class="abs" style="left:112px;top:1582px"><div class="card-name">HUNDESCHULE</div><div class="card-text">Welpenförderung Agility Mantrailing</div></div>

<div class="abs tab green" style="left:486px;top:1310px"><span class="tab-label">NOTHELFER</span></div>
<div class="abs card-img" style="left:436px;top:1338px;background:linear-gradient(150deg,#8cc2a8,#e9e6e0 55%,#d84a3c)" role="img" aria-label="Foto: Sanitäterin mit Stethoskop und Herz"></div>
<div class="abs" style="left:436px;top:1582px"><div class="card-name">NOTHELFER</div><div class="card-text">Auffrischungskurs<br>Gutschein für Fahrstunden bei uns</div></div>

<div class="abs tab brown" style="left:810px;top:1310px"><span class="tab-label">SANITÄTSSCHULUNG</span></div>
<div class="abs card-img" style="left:760px;top:1338px;background:linear-gradient(150deg,#c8ccd0,#eeeeee 50%,#9aa2a8)" role="img" aria-label="Foto: Person in weissem Schutzanzug"></div>
<div class="abs" style="left:760px;top:1582px"><div class="card-name">SANITÄTSSCHULUNG</div><div class="card-text">Auffrischungskurs</div></div>

<!-- row 3 -->
<div class="abs tab green" style="left:162px;top:1738px"><span class="tab-label">BLS AGD</span></div>
<div class="abs card-img" style="left:112px;top:1766px;background:linear-gradient(160deg,#a9c6de,#e8ebe6 50%,#8a9a5c)" role="img" aria-label="Foto: Zug auf Gleisen"></div>
<div class="abs" style="left:112px;top:2010px"><div class="card-name">BLS AGD</div><div class="card-text">Auffrischungskurs</div></div>

<div class="abs tab brown" style="left:486px;top:1738px"><span class="tab-label">CZV</span></div>
<div class="abs card-img" style="left:436px;top:1766px;background:linear-gradient(160deg,#3e4e6c,#22262c 55%,#6a5a4a)" role="img" aria-label="Foto: Lastwagen bei Nacht"></div>
<div class="abs" style="left:436px;top:2010px"><div class="card-name">CZV</div><div class="card-text">Berufsfahrer Weiterbildung<br>Arbeits- und Ruhezeitverordnung<br>Eco-Drive Fahrzeugtechnik</div></div>

<div class="abs tab green" style="left:810px;top:1738px"><span class="tab-label">BERGAUSBILDUNG</span></div>
<div class="abs card-img" style="left:760px;top:1766px;background:linear-gradient(170deg,#8fa4b6,#6f7a6a 55%,#4a4e44)" role="img" aria-label="Foto: Wanderer in den Bergen"></div>
<div class="abs" style="left:760px;top:2010px"><div class="card-name">BERGAUSBILDUNG</div><div class="card-text">Bergführer<br>Touren<br>Erste Hilfe</div></div>

<!-- about -->
<div class="abs deco" style="left:805px;top:2150px">Ü</div>
<div class="abs about-frame"></div>
<div class="abs about-img" role="img" aria-label="Foto: Kursleiterteam mit Hunden unter einem Baum"></div>
<h2 class="abs about-title">Über uns</h2>
<p class="abs about-text">In meinen beruflichen Laufbahn erlebte ich immer wieder Situationen, welche in mir die Idee reifen liessen, jeden interessierten Menschen ein Grundwissen zukommen zu lassen, welches ihn bei einer Notsituation ruhig und mit den richtigen Ruhe reagieren lässt. Das Zusammenlegen und Kombinieren von Wissen und Fertigkeiten der verschiedenen Fachbereiche gibt dem Menschen Sicherheit und Vertrauen in seinem Handeln. Aus eigener Erfahrung hat sich gezeigt, je professioneller man auf Gefahrensituationen vorbereitet ist, desto sicherer und erfolgreicher kann eine Notfallsituation gemeistert und Leben gerettet werden.</p>

<!-- goal -->
<div class="abs goal"></div>
<p class="abs goal-text">Ziel: Professionelles, sicheres und ruhiges<br>Agieren in allen Situationen!</p>
<span class="abs btn goal-btn">OUR COURSE</span>

<!-- footer -->
<footer class="abs footer"></footer>
<div class="abs foot-brand"><span class="brand-dot"></span><span class="brand-name">moluvo.ch</span></div>
<div class="abs contact">
  <span><svg width="14" height="18" viewBox="0 0 14 18"><path d="M7 0C3.1 0 0 3.1 0 7c0 5 7 11 7 11s7-6 7-11c0-3.9-3.1-7-7-7zm0 10a3 3 0 110-6 3 3 0 010 6z" fill="#fff"/></svg>Talweg 27, CH-3900 Brig</span>
  <span><svg width="16" height="16" viewBox="0 0 16 16"><path d="M3 1l3 3-2 2c1 2 3 4 5 5l2-2 3 3-2 3C6 14 2 10 1 3z" fill="#fff"/></svg>Telefon: +41 79 000 12 34</span>
  <span><svg width="18" height="13" viewBox="0 0 18 13"><rect x="0.5" y="0.5" width="17" height="12" fill="#fff"/><path d="M1 1l8 6 8-6" stroke="#30363c" fill="none"/></svg>E-Mail: info@moluvo.ch</span>
</div>
<p class="abs copy">© Copyright bei moluvo.ch 2021</p>

</body>
</html>
```